Verodex business card

Business card for sustainable investment company called "Verodex". Verodex is an exchange platform selling carbon credits between buyers and sellers. Carbon Credits are an environmental commodity for reducing global carbon emissions.

the card should obviously have our logo and the theme should be sustainability/environment mixed with a trading platform.

Contact Information for Business Card

Logo, Name, Title, Phone, Email

Colors
0054AA
0677BA
7BADD7
CADEEF
E8F1F8
0094D4
00A9DD
6FCCEA
C7EBF8
E9F6FB
00AB8E
00BBA5
67D7C9
C6EFE9
E9F9F6
59FF00
82FF00
B8FF75
E3FFCB
F4FFEA

```html
<!DOCTYPE html>
<html lang="en">
<head>
<meta charset="UTF-8">
<title>Verodex Business Card</title>
<link rel="stylesheet" href="https://fonts.googleapis.com/css2?family=Lexend:wght@300;400;600;700&display=swap">
<style>
  :root {
    --page-bg: #e4e4e2;
    --navy-dark: #16243d;
    --navy: #1e2f4b;
    --navy-light: #2e435c;
    --navy-deep: #0e1a2e;
    --paper: #f7f7f7;
    --paper-shade: #ececec;
    --brand-blue: #0094D4;
    --name-blue: #3f8ec8;
    --ink-light: #eef2f6;
  }
  * { box-sizing: border-box; margin: 0; padding: 0; }
  html, body { width: 1200px; height: 1200px; overflow: hidden; }
  body {
    background: var(--page-bg);
    font-family: "Lexend", sans-serif;
    position: relative;
  }
  .card {
    position: absolute;
    left: 235px;
    width: 730px;
    height: 418px;
    overflow: hidden;
  }
  .card-front {
    top: 160px;
    background: linear-gradient(30deg, var(--navy-dark) 0%, var(--navy) 50%, var(--navy-light) 100%);
    display: flex;
    align-items: center;
    justify-content: center;
  }
  .wordmark {
    display: flex;
    align-items: center;
    gap: 22px;
  }
  .wordmark-dot {
    width: 58px;
    height: 58px;
    border-radius: 50%;
    background: var(--brand-blue);
  }
  .wordmark-name {
    font-weight: 600;
    font-size: 62px;
    letter-spacing: 1px;
    color: #ffffff;
    line-height: 1;
  }
  .card-back {
    top: 632px;
    background: linear-gradient(120deg, var(--paper) 0%, var(--paper-shade) 100%);
  }
  .back-wordmark {
    position: absolute;
    left: 55px;
    top: 40px;
    gap: 14px;
  }
  .back-wordmark .wordmark-dot { width: 40px; height: 40px; }
  .back-wordmark .wordmark-name { font-size: 37px; color: var(--navy); }
  .wave {
    position: absolute;
    left: 0;
    top: 0;
    width: 730px;
    height: 418px;
  }
  .person {
    position: absolute;
    left: 67px;
    top: 278px;
  }
  .person-name {
    font-weight: 700;
    font-size: 33px;
    color: var(--name-blue);
    line-height: 1.1;
  }
  .person-title {
    font-weight: 300;
    font-size: 19px;
    color: var(--ink-light);
    margin-top: 6px;
  }
  .contact {
    position: absolute;
    left: 353px;
    top: 241px;
    color: var(--ink-light);
    font-weight: 300;
    font-size: 19px;
  }
  .contact-line {
    display: flex;
    align-items: center;
    gap: 9px;
    height: 28px;
  }
  .contact-line svg { width: 15px; height: 15px; flex: none; }
  .office-name {
    font-weight: 700;
    font-size: 19px;
    margin-top: 6px;
  }
  .office-address { margin-top: 4px; }
</style>
</head>
<body>
  <section class="card card-front">
    <div class="wordmark">
      <span class="wordmark-dot"></span>
      <span class="wordmark-name">VERODEX</span>
    </div>
  </section>

  <section class="card card-back">
    <div class="wordmark back-wordmark">
      <span class="wordmark-dot"></span>
      <span class="wordmark-name">VERODEX</span>
    </div>

    <svg class="wave" viewBox="0 0 1176 673" preserveAspectRatio="none">
      <defs>
        <linearGradient id="bandFill" x1="0" y1="0" x2="1" y2="0">
          <stop offset="0" stop-color="#1b2a45"/>
          <stop offset="1" stop-color="#253a58"/>
        </linearGradient>
      </defs>
      <path d="M0,295 C200,360 420,385 620,322 C820,262 1010,248 1176,268 L1176,673 L0,673 Z" fill="var(--navy-deep)"/>
      <path d="M0,380 C250,428 450,378 650,323 C850,278 1050,296 1176,352 L1176,673 L0,673 Z" fill="url(#bandFill)"/>
      <path d="M0,370 C250,418 450,368 650,313 C850,268 1050,286 1176,342" fill="none" stroke="#f4f4f4" stroke-width="9"/>
    </svg>

    <div class="person">
      <p class="person-name">Marek Halden</p>
      <p class="person-title">Sales Representative</p>
    </div>

    <div class="contact">
      <p class="contact-line">
        <svg viewBox="0 0 16 16" aria-hidden="true"><path d="M3.5 1.5l2.2 2.4-1.2 1.8c.9 2 2.4 3.5 4.3 4.4l1.8-1.2 2.4 2.2-1.4 2.4C6.8 13.3 2.7 9.2 1.2 4.4z" fill="#eef2f6"/><path d="M9.5 2.5a4 4 0 0 1 4 4M9.5 0.8a5.7 5.7 0 0 1 5.7 5.7" fill="none" stroke="#eef2f6" stroke-width="1.2"/></svg>
        <span>+36 30 555 0142</span>
      </p>
      <p class="contact-line">
        <svg viewBox="0 0 16 16" aria-hidden="true"><rect x="1" y="3" width="14" height="10" rx="1" fill="#eef2f6"/><path d="M1.5 3.8L8 9l6.5-5.2" fill="none" stroke="#1e2f4b" stroke-width="1.3"/></svg>
        <span>szerviz@verodex.com</span>
      </p>
      <p class="contact-line">
        <svg viewBox="0 0 16 16" aria-hidden="true"><circle cx="8" cy="8" r="6.6" fill="#eef2f6"/><path d="M1.5 8h13M8 1.5c-3 3.5-3 9.5 0 13M8 1.5c3 3.5 3 9.5 0 13" fill="none" stroke="#1e2f4b" stroke-width="1.1"/></svg>
        <span>www.verodex.com</span>
      </p>
      <p class="office-name">Verodex Head Office</p>
      <p class="office-address">Budapest XIII. Tavasz utca 14.</p>
    </div>
  </section>
</body>
</html>
```